NEW Modern Sleek Business Card for VR Language Startup

Our startup is using VR to lead the next wave of world language education. We need a two-sided business card that introduces the larger organization (Brightloom Language Inc) and our contact info on one side and shows the product, Glimwoorld, on the other side.

Side 1 (contact info)= Brightloom Logo and Contact info (name, title, phone, email)

Side 2 (product)= Glimworld logo, text, and website
Text= Culturally Immersive Language Learning Games
Website= www.glimworld-play.com

Target Market(s)

Education, Technology

Contact Information for Business Card

Contact info will be updated upon approval of the design. For now, put this as a placeholder.

Perry Dunmore
Founder & CEO
pdunmore@quillpost-mail.net
(555)-014-2286

Font styles to use
Other font styles liked:
• Gibson and Century Gothic are the brand fonts

Requirements
Nice to have
• I would love to see cohesion between the design and colors of the two logos. I have attached a few business card designs that I like, so you can get a feel for my preferred style.

```html
<!DOCTYPE html>
<html lang="en">
<head>
<meta charset="utf-8">
<title>Brightloom Language — Business Card</title>
<link rel="stylesheet" href="https://fonts.googleapis.com/css2?family=Montserrat:wght@600&family=Questrial&display=swap">
<style>
  :root {
    --page-bg: #e6e6e6;
    --card-light: #ffffff;
    --card-dark: #222222;
    --ink: #1f1f1f;
    --ink-soft: #2a2a2a;
    --accent-red: #e8344e;
    --accent-orange: #f0864a;
    --accent-blue: #36c1e6;
  }
  * { box-sizing: border-box; margin: 0; padding: 0; }
  html, body { width: 1200px; height: 1200px; overflow: hidden; }
  body {
    background: var(--page-bg);
    font-family: "Questrial", "Century Gothic", sans-serif;
    position: relative;
  }
  .card {
    position: absolute;
    left: 240px;
    width: 720px;
    height: 420px;
    border-radius: 32px;
    overflow: hidden;
  }
  .card--front { top: 142px; background: var(--card-light); }
  .card--back { top: 638px; background: var(--card-dark); }

  .brand {
    position: absolute;
    display: flex;
    align-items: center;
    gap: 12px;
  }
  .brand__dot {
    width: 74px; height: 74px;
    border-radius: 50%;
    background: var(--accent-red);
    flex: none;
  }
  .brand__name {
    font-family: "Montserrat", sans-serif;
    font-weight: 600;
    line-height: 1;
    color: var(--ink-soft);
    white-space: nowrap;
  }
  .brand__name span { display: block; }
  .brand__word { font-size: 24px; letter-spacing: 2px; }
  .brand__sub { font-size: 13px; letter-spacing: 6.5px; margin-top: 8px; padding-left: 4px; }

  .card--front .brand { left: 48px; top: 180px; }

  .card--back .brand { left: 50%; top: 160px; transform: translateX(-50%); gap: 16px; }
  .card--back .brand__name { color: #ffffff; }
  .card--back .brand__dot { width: 100px; height: 100px; }
  .card--back .brand__word { font-size: 36px; letter-spacing: 4px; }
  .card--back .brand__sub { font-size: 18px; letter-spacing: 8px; margin-top: 10px; padding-left: 10px; }

  .divider {
    position: absolute;
    left: 360px; top: 156px;
    width: 2px; height: 122px;
    background: linear-gradient(var(--accent-red), var(--accent-orange));
  }
  .contact { position: absolute; left: 385px; top: 148px; }
  .contact__name {
    font-family: "Montserrat", sans-serif;
    font-weight: 600;
    font-size: 22px;
    letter-spacing: 1.5px;
    color: var(--accent-red);
    text-transform: uppercase;
  }
  .contact__title { font-size: 18px; color: var(--ink); margin-top: 8px; }
  .contact__list { list-style: none; margin-top: 22px; }
  .contact__item {
    display: flex; align-items: center; gap: 12px;
    font-size: 17px; color: var(--ink); height: 32px;
  }
  .contact__icon { width: 13px; height: 13px; flex: none; }

  .tagline {
    position: absolute; left: 0; right: 0; top: 320px;
    text-align: center; color: #ffffff; font-size: 18px;
  }
  .web-row {
    position: absolute; left: 0; right: 0; top: 364px;
    display: flex; align-items: center; gap: 16px;
  }
  .web-row__line { flex: 1; height: 1px; }
  .web-row__line--left { background: linear-gradient(90deg, var(--accent-red), var(--accent-blue)); }
  .web-row__line--right { background: linear-gradient(90deg, var(--accent-blue), var(--accent-red)); }
  .web-row__url { color: #ffffff; font-size: 17px; }
</style>
</head>
<body>
  <section class="card card--front" aria-label="Business card front">
    <div class="brand">
      <div class="brand__dot"></div>
      <div class="brand__name">
        <span class="brand__word">BRIGHTLOOM</span>
        <span class="brand__sub">LANGUAGE</span>
      </div>
    </div>
    <div class="divider"></div>
    <div class="contact">
      <h1 class="contact__name">Perry Dunmore</h1>
      <p class="contact__title">Founder &amp; CEO</p>
      <ul class="contact__list">
        <li class="contact__item">
          <svg class="contact__icon" viewBox="0 0 16 16" aria-hidden="true"><path fill="#e8344e" d="M3.5 1l2.5 3-1.6 1.6c.8 2 2.5 3.7 4.5 4.5L10.5 8.5l3 2.5-1.2 2.6C7 13.5 2.5 9 2.4 3.7z"/></svg>
          (555)-014-2286
        </li>
        <li class="contact__item">
          <svg class="contact__icon" viewBox="0 0 16 16" aria-hidden="true"><rect x="1" y="3" width="14" height="10" rx="1" fill="#e8344e"/><path d="M2 4l6 5 6-5" fill="none" stroke="#fff" stroke-width="1.4"/></svg>
          pdunmore@quillpost-mail.net
        </li>
      </ul>
    </div>
  </section>

  <section class="card card--back" aria-label="Business card back">
    <div class="brand">
      <div class="brand__dot"></div>
      <div class="brand__name">
        <span class="brand__word">GLIMWORLD</span>
        <span class="brand__sub">LANGUAGE</span>
      </div>
    </div>
    <p class="tagline">Culturally Immersive Language Learning Games</p>
    <div class="web-row">
      <span class="web-row__line web-row__line--left"></span>
      <span class="web-row__url">www.glimworld-play.com</span>
      <span class="web-row__line web-row__line--right"></span>
    </div>
  </section>
</body>
</html>
```